A Vegan Nutritional Supplement (one Product) website

I am looking for an experienced Web designer to build a One Product website for a Nutritional Supplement that is 100% vegan. The emphasis would be on both the Quality and Quantity of the ingredients and their benefits. It contains Essential Vitamins, Minerals, and a proprietary blend of 42 Fruits and Vegetables. I welcome color suggestions as long as it includes Green (vegan) and White.. The final design should communicate to the buyer: Quality, Healthy, Safety (Natural vegan ingredients), Natural energy, well being. The product includes benefits for 3 vital elements of optimal health: Immune Health, Heart Health, and Brain Health

Industry/Entity Type

Health and Wellness - Nutritional Supplements

Number of Pages Required

4 page

Other font styles liked:
• I Welcome your creativity

Colors
59FF00
82FF00
B8FF75
E3FFCB
F4FFEA

Requirements
Must have
• Options to purchase : One product ($34.95); 2 products ($31.45 each - 10% discount), or 3 Products ($27.95 each - 20% discount)
Nice to have
• Focus on the Benefits of having all these Ingredients - Nutrients in one bottle - Essential Vitamins, Minerals, and proprietary blend of 42 Fruits and Vegetables.

```html
<!DOCTYPE html>
<html lang="en">
<head>
<meta charset="utf-8">
<title>Plant Vigor – Verdalia</title>
<link href="https://fonts.googleapis.com/css2?family=Roboto:ital,wght@0,400;0,500;0,700;1,400&display=swap" rel="stylesheet">
<style>
:root{
  --green-dark:#1b6b27;
  --green:#1f7a2c;
  --green-deep:#155720;
  --lime:#7cc42a;
  --ink:#222;
  --muted:#666;
  --grey-bg:#efefef;
  --white:#fff;
}
*{box-sizing:border-box;margin:0;padding:0}
html,body{width:1200px;height:3585px;overflow:hidden}
body{font-family:"Roboto",Arial,sans-serif;color:var(--ink);background:var(--white);position:relative}
.abs{position:absolute}
/* nav */
.nav{left:0;top:0;width:1200px;height:61px;background:var(--green)}
.brand{left:111px;top:14px;color:var(--white);font-size:24px;font-weight:500;display:flex;align-items:center;gap:8px}
.brand-dot{width:22px;height:22px;border-radius:50%;background:var(--lime)}
.menu{right:110px;top:20px;display:flex;gap:28px;font-size:15px;color:var(--white)}
.menu .active{position:relative}
.menu .active:after{content:"";position:absolute;left:50%;top:30px;margin-left:-9px;border:9px solid transparent;border-bottom-color:var(--white);border-top:0}
/* hero */
.hero-photo{left:0;top:61px;width:1200px;height:700px;background:linear-gradient(110deg,#2a2f2c 0%,#3f4541 45%,#2b302d 100%)}
.hero-title{left:111px;top:262px;font-size:64px;font-weight:700;color:var(--white)}
.hero-text{left:111px;top:347px;width:445px;font-size:14.5px;line-height:26px;color:var(--white)}
.btn{display:flex;align-items:center;justify-content:center;background:var(--lime);color:var(--green-deep);font-weight:500;font-size:15px;border-radius:0 34px 0 34px;letter-spacing:.3px}
.hero-btn{left:111px;top:447px;width:231px;height:60px}
.hero-blob{left:647px;top:165px;width:406px;height:406px;border-radius:50%;background:var(--lime)}
.bottle{border-radius:24px 24px 16px 16px;background:linear-gradient(180deg,#f2f2f2 0 18%,#3f8d3a 18% 70%,#d9c14d 70% 82%,#3f8d3a 82%)}
.hero-bottle{left:717px;top:153px;width:243px;height:439px}
/* about */
h2{font-size:42px;font-weight:700;text-align:center;color:var(--ink)}
.about-title{left:0;top:776px;width:1200px}
.about-text{left:118px;top:852px;width:964px;font-size:14px;line-height:26px;text-align:center;color:var(--muted)}
.about-text p+p{margin-top:8px}
.about-btn{left:484px;top:1036px;width:231px;height:60px;box-shadow:0 8px 14px rgba(0,0,0,.12)}
/* products */
.products-title{left:0;top:1300px;width:1200px;color:var(--white)}
.card{top:1381px;width:309px;height:369px;background:var(--white);border-radius:0 0 34px 0;text-align:center;box-shadow:0 6px 16px rgba(0,0,0,.15)}
.card-tag{position:absolute;right:12px;top:13px;font-size:13px;color:#444}
.card-img{position:absolute;left:0;right:0;top:36px;height:162px;display:flex;justify-content:center;gap:2px}
.card-img .bottle{width:90px;height:162px}
.card-name{position:absolute;left:0;right:0;top:220px;font-size:19px;font-weight:700;color:var(--green)}
.card-text{position:absolute;left:18px;right:18px;top:254px;font-size:13px;line-height:26px;color:var(--muted)}
.card-price{position:absolute;left:0;right:0;top:315px;font-size:20px;font-weight:700;color:var(--green)}
.card-price small{font-size:13px;font-weight:400;color:var(--muted)}
/* benefits */
.benefits-title{left:0;top:1953px;width:1200px}
.benefit{left:113px;width:470px;display:flex;gap:15px}
.b-icon{width:97px;height:97px;border-radius:50%;background:var(--green-dark);flex:none;display:flex;align-items:center;justify-content:center}
.b-body{padding-top:10px}
.b-body h3{font-size:16px;font-weight:500;letter-spacing:.5px;margin-bottom:8px}
.b-body p{font-size:13px;line-height:24px;color:var(--muted);letter-spacing:.4px}
.benefit-bottle{left:689px;top:2057px;width:299px;height:546px}
/* testimonials */
.testi-bg{left:0;top:2673px;width:1200px;height:520px;background:var(--grey-bg)}
.testi-title{left:0;top:2727px;width:1200px}
.avatar{border-radius:50%;background:linear-gradient(160deg,#cdbba6,#8a7a68)}
.av-side{top:2807px;width:86px;height:86px;opacity:.45;border:3px solid var(--lime)}
.av-main{left:544px;top:2794px;width:112px;height:112px;border:4px solid var(--lime)}
.quote{left:218px;top:2925px;width:764px;font-size:14px;line-height:26px;font-style:italic;text-align:center;color:#555}
.arrow{top:2960px;font-size:30px;color:#222}
.t-name{left:0;top:3058px;width:1200px;text-align:center;color:var(--green);font-size:17px;font-weight:500}
.t-role{left:0;top:3088px;width:1200px;text-align:center;color:#555;font-size:14px}
/* footer */
.f-title{left:111px;top:3308px;font-size:32px;font-weight:700;color:var(--white)}
.f-text{left:111px;top:3368px;width:365px;font-size:13px;line-height:26px;color:var(--white)}
.f-head{top:3300px;font-size:19px;font-weight:500;color:var(--white)}
.f-links{top:3346px;list-style:none;font-size:13.5px;color:var(--white);line-height:29px}
.f-links li:before{content:"» ";font-size:15px;margin-right:4px}
.phone{left:895px;top:3344px;display:flex;align-items:center;gap:8px;color:var(--white);font-size:17px;font-weight:700}
.phone-ring{width:34px;height:34px;border-radius:50%;border:1.5px solid var(--white);display:flex;align-items:center;justify-content:center}
.socials{left:905px;top:3406px;display:flex;gap:16px}
.socials span{width:30px;height:30px;background:var(--white)}
.bottom-bar{left:0;top:3528px;width:1200px;height:57px;background:#0f4a18;color:var(--white);text-align:center;font-size:15px;font-weight:500;line-height:57px}
</style>
</head>
<body>

<header>
  <div class="abs nav"></div>
  <div class="abs brand"><span class="brand-dot"></span>Verdalia</div>
  <nav class="abs menu">
    <span class="active">Home</span><span>About</span><span>Products</span><span>Benefits</span><span>Blog</span><span>Contact</span>
    <span>
      <svg width="14" height="12" viewBox="0 0 14 12" fill="#fff"><path d="M0 0h3l1 2h10l-2 6H5L2 1H0z"/><circle cx="6" cy="10.5" r="1.3"/><circle cx="11" cy="10.5" r="1.3"/></svg>
      Cart (0)</span>
  </nav>
</header>

<section class="hero">
  <div class="abs hero-photo" role="img" aria-label="Photo of a woman resting on an exercise bike in a dark gym"></div>
  <div class="abs hero-blob"></div>
  <div class="abs bottle hero-bottle" role="img" aria-label="Plant Vigor supplement bottle"></div>
  <svg class="abs" style="left:0;top:590px" width="1200" height="175" viewBox="0 0 1200 175">
    <path d="M0 170 C200 20 420 -20 620 60 S950 140 1200 70 V175 H0Z" fill="#1f7a2c"/>
    <path d="M0 175 C220 110 420 90 640 130 S980 175 1200 150 V175Z" fill="#fff"/>
  </svg>
  <h1 class="abs hero-title">Plant Vigor</h1>
  <p class="abs hero-text">When healthy food is a nuisance, a weak immune system, the risk of<br>chronic and mental illnesses in old age is quite common. According to<br>one report of Veldra Health,</p>
  <div class="abs btn hero-btn">GET STARTED</div>
</section>

<section class="about">
  <h2 class="abs about-title">About Us</h2>
  <div class="abs about-text">
    <p>Lorem ipsum dolor sit amet, consectetur adipiscing elit, sed do eiusmod tempor incididunt ut labore et dolore magna aliqua. Ut enim ad minim veniam, quis nostrud exercitation ullamco laboris nisi ut aliquip ex ea commodo consequat. Duis aute irure dolor in reprehenderit in voluptate velit esse cillum dolore eu fugiat nulla pariatur. Excepteur sint occaecat cupidatat non proident, sunt in culpa qui officia deserunt mollit anim id est laborum</p>
    <p>Lorem ipsum dolor sit amet, consectetur adipiscing elit, sed do eiusmod tempor incididunt ut labore et dolore magna aliqua. Ut enim ad minim veniam, quis nostrud exercitation ullamco laboris nisi ut aliquip ex ea commodo consequat. Duis aute irure dolor in reprehenderit in voluptate velit esse cillum dolore eu fugiat nulla pariatur. Excepteur sint occaecat cupidatat non proident, sunt in culpa qui officia deserunt mollit anim id est laborum</p>
  </div>
  <div class="abs btn about-btn">READ MORE</div>
</section>

<section class="products">
  <svg class="abs" style="left:0;top:1185px" width="1200" height="690" viewBox="0 0 1200 690">
    <path d="M0 88 Q600 -60 1200 88 V600 Q600 760 0 600Z" fill="#1b6b27"/>
  </svg>
  <h2 class="abs products-title">Our Products</h2>
  <div class="abs card" style="left:111px">
    <div class="card-img"><div class="bottle" role="img" aria-label="One bottle"></div></div>
    <div class="card-name">One Product</div>
    <div class="card-text">Lorem ipsum dolor sit amet, adipiscing elit, sed do eiusmod tempor incididunt ut labore</div>
    <div class="card-price">$34.95</div>
  </div>
  <div class="abs card" style="left:445px">
    <div class="card-tag">10% discount</div>
    <div class="card-img" role="img" aria-label="Two bottles"><div class="bottle"></div><div class="bottle"></div></div>
    <div class="card-name">2 Products</div>
    <div class="card-text">Lorem ipsum dolor sit amet, adipiscing elit, sed do eiusmod tempor incididunt ut labore</div>
    <div class="card-price">$34.95 <small>each</small></div>
  </div>
  <div class="abs card" style="left:780px">
    <div class="card-tag">20% discount</div>
    <div class="card-img" role="img" aria-label="Three bottles" style="gap:0"><div class="bottle" style="width:64px"></div><div class="bottle"></div><div class="bottle" style="width:64px"></div></div>
    <div class="card-name">3 Products</div>
    <div class="card-text">Lorem ipsum dolor sit amet, adipiscing elit, sed do eiusmod tempor incididunt ut labore</div>
    <div class="card-price">$27.95 <small>each</small></div>
  </div>
</section>

<section class="benefits">
  <h2 class="abs benefits-title">Product Benefits</h2>
  <div class="abs benefit" style="top:2046px">
    <div class="b-icon"><svg width="54" height="54" viewBox="0 0 54 54" fill="none" stroke="#fff" stroke-width="2"><circle cx="27" cy="27" r="22"/><circle cx="27" cy="27" r="14"/><path d="M20 27l5 5 9-10"/></svg></div>
    <div class="b-body"><h3>Quality</h3><p>Lorem ipsum dolor sit amet, consectetur adipiscing elit,<br>sed do eiusmod tempor incididunt ut</p></div>
  </div>
  <div class="abs benefit" style="top:2156px">
    <div class="b-icon"><svg width="54" height="54" viewBox="0 0 54 54" fill="none" stroke="#fff" stroke-width="2"><path d="M27 22c-3-6-12-4-10 3 1 4 10 10 10 10s9-6 10-10c2-7-7-9-10-3z"/><path d="M8 40c8-2 14 2 19 8 5-6 11-10 19-8"/></svg></div>
    <div class="b-body"><h3>Healthy</h3><p>Lorem ipsum dolor sit amet, consectetur adipiscing elit,<br>sed do eiusmod tempor incididunt ut</p></div>
  </div>
  <div class="abs benefit" style="top:2265px">
    <div class="b-icon"><svg width="54" height="54" viewBox="0 0 54 54" fill="none" stroke="#fff" stroke-width="2"><path d="M27 8l13 5v10c0 9-6 14-13 17-7-3-13-8-13-17V13z"/><path d="M21 24l5 5 8-9"/><path d="M8 46h30l8-6"/></svg></div>
    <div class="b-body"><h3>Safety</h3><p>Lorem ipsum dolor sit amet, consectetur adipiscing elit,<br>sed do eiusmod tempor incididunt ut</p></div>
  </div>
  <div class="abs benefit" style="top:2375px">
    <div class="b-icon"><svg width="54" height="54" viewBox="0 0 54 54" fill="none" stroke="#fff" stroke-width="2"><path d="M30 8L18 30h9l-3 16 12-22h-9z"/><path d="M8 27h5M41 27h5M13 13l4 4M41 13l-4 4M13 41l4-4M41 41l-4-4"/></svg></div>
    <div class="b-body"><h3>Natural Energy</h3><p>Lorem ipsum dolor sit amet, consectetur adipiscing elit,<br>sed do eiusmod tempor incididunt ut</p></div>
  </div>
  <div class="abs benefit" style="top:2484px">
    <div class="b-icon"><svg width="54" height="54" viewBox="0 0 54 54" fill="none" stroke="#fff" stroke-width="2"><circle cx="27" cy="14" r="5"/><path d="M27 20v14M15 28l12-4 12 4M12 44l15-8 15 8H12z"/></svg></div>
    <div class="b-body"><h3>Well Being</h3><p>Lorem ipsum dolor sit amet, consectetur adipiscing elit,<br>sed do eiusmod tempor incididunt ut</p></div>
  </div>
  <div class="abs bottle benefit-bottle" role="img" aria-label="Plant Vigor supplement bottle"></div>
</section>

<section class="testimonials">
  <div class="abs testi-bg"></div>
  <h2 class="abs testi-title">Testimonials</h2>
  <div class="abs avatar av-side" style="left:441px" role="img" aria-label="Customer portrait"></div>
  <div class="abs avatar av-main" role="img" aria-label="Customer portrait"></div>
  <div class="abs avatar av-side" style="left:673px" role="img" aria-label="Customer portrait"></div>
  <div class="abs arrow" style="left:128px">⟵</div>
  <div class="abs arrow" style="left:1028px">⟶</div>
  <p class="abs quote">Lorem ipsum dolor sit amet, consectetur adipiscing elit, sed do eiusmod tempor incididunt ut labore et dolore magna aliqua. Ut enim ad minim veniam, quis nostrud exercitation ullamco laboris nisi ut aliquip ex ea commodo consequat. Duis aute irure dolor in reprehenderit in voluptate velit esse cillum dolore eu fugiat nulla pariatur. Excepteur sint occaecat cupidatat non proident, sunt in culpa qui officia deserunt mollit anim id est laborum</p>
  <div class="abs t-name">Dana Morrow</div>
  <div class="abs t-role">Lorem ipsum dolor</div>
</section>

<footer>
  <svg class="abs" style="left:0;top:3100px" width="1200" height="430" viewBox="0 0 1200 430">
    <path d="M0 50 C250 -10 500 130 800 90 S1100 10 1200 40 V430 H0Z" fill="#7cc42a"/>
    <path d="M0 50 C260 20 520 150 820 120 S1100 60 1200 90 V430 H0Z" fill="#1b6b27"/>
  </svg>
  <div class="abs f-title">About Us</div>
  <p class="abs f-text">Lorem ipsum dolor sit amet, consectetur adipiscing elit, sed do eiusmod tempor incididunt ut labore et dolore magna aliqua. Ut enim ad minim veniam, quis nostrud exercitation ullamco laboris nisi ut aliquip ex ea commodo consequat. Duis aute irure dolor in reprehenderit</p>
  <div class="abs f-head" style="left:537px">Quick Links</div>
  <ul class="abs f-links" style="left:537px"><li>Home</li><li>About Us</li><li>Products</li><li>Benefits</li><li>Contact Us</li></ul>
  <ul class="abs f-links" style="left:722px"><li>Reviews</li><li>FAQ's</li><li>Help</li></ul>
  <div class="abs f-head" style="left:895px">Contact Us</div>
  <div class="abs phone"><span class="phone-ring"><svg width="16" height="16" viewBox="0 0 16 16" fill="none" stroke="#fff" stroke-width="1.4"><path d="M3 1l3 3-2 2c1 2 3 4 5 5l2-2 3 3-2 2C7 14 2 9 1 3z"/></svg></span>+1 555 010 2040</div>
  <div class="abs socials"><span></span><span></span><span></span><span></span></div>
  <div class="abs bottom-bar">© 2022 All Rights Reserved</div>
</footer>

</body>
</html>
```